Website Re-design for Kids Playhouse Business

Need current website which looks very outdated to be re-designed to look modern and contemporary, reduce clutter significantly and make it look elegant and simple.
Current website: http://www.tumblenest.com.au/
A website which the business owner likes, use as reference/inspiration: http://vexa.com.au/
Looking for light green palette, natural colours. "WHAT'S ON" page/link no longer required.
Industry/Entity Type
Business
Number of Pages Required
5+ page
Look and feel
Each slider illustrates characteristics of the customer's brand and the style your logo design should communicate.

```html
<!DOCTYPE html>
<html lang="en">
<head>
<meta charset="utf-8">
<title>Tumble Nest Playhouse &amp; Cafe</title>
<link href="https://fonts.googleapis.com/css2?family=Montserrat:wght@400;500;600;700&family=Open+Sans:ital,wght@0,400;0,600;1,400&display=swap" rel="stylesheet">
<style>
:root{
  --green:#7cc242;
  --green-dark:#5fa52b;
  --green-light:#a6d86e;
  --ink:#333333;
  --muted:#8a8a8a;
  --line:#dddddd;
  --white:#ffffff;
  --sun:#f7a823;
  --sun-light:#fcc93a;
  --sun-dark:#e8931a;
}
*{margin:0;padding:0;box-sizing:border-box}
html,body{width:1200px;height:3064px;overflow:hidden;background:var(--white)}
body{font-family:"Open Sans",Arial,sans-serif;color:var(--ink);position:relative}
.canvas{position:relative;width:1200px;height:3064px;overflow:hidden}
.abs{position:absolute}
.head{font-family:"Montserrat",Arial,sans-serif}

/* hero */
.hero-photo{left:0;top:0;width:1200px;height:680px;background:linear-gradient(120deg,#e6d9cf 0%,#f1c9d3 35%,#d9c2b4 60%,#b9cfe0 100%)}
.brand{left:40px;top:32px;width:176px;height:96px;background:var(--white);border-radius:8px;display:flex;flex-direction:column;justify-content:center;align-items:center;font-family:"Montserrat",sans-serif;font-weight:700;color:var(--green-dark);font-size:20px;line-height:1.15;text-align:center}
.hero-badge{left:96px;top:188px;width:372px;height:372px;border-radius:50%;background:rgba(124,194,66,.88);border:8px solid rgba(255,255,255,.55);color:var(--white);text-align:center;padding-top:88px}
.hero-badge .kicker{font-family:"Montserrat",sans-serif;font-size:22px;font-weight:500}
.hero-badge h1{font-family:"Montserrat",sans-serif;font-size:34px;font-weight:600;line-height:1.2;margin-top:8px}
.hero-badge p{font-size:13px;line-height:1.5;margin:14px auto 0;width:230px;opacity:.9}
.dots{display:flex;gap:10px;justify-content:center;margin-top:24px}
.dots span{width:12px;height:12px;border-radius:50%;background:var(--white)}
.dots span:first-child{background:transparent;border:2px solid var(--white)}

/* about */
.about-photo{left:40px;top:690px;width:480px;height:380px;background:radial-gradient(circle at 40% 45%,#f1d8c4 0%,#e9ece8 60%,#ffffff 100%)}
.about-title{left:612px;top:742px;font-family:"Montserrat",sans-serif;font-size:34px;font-weight:600;line-height:1.15;color:var(--ink)}
.about-text{left:612px;top:840px;width:520px;font-size:14px;line-height:1.75;color:var(--muted)}
.btn{display:inline-flex;align-items:center;justify-content:center;border-radius:30px;font-family:"Montserrat",sans-serif;font-weight:600}
.btn-outline{left:612px;top:1006px;width:162px;height:52px;border:2px solid var(--green);color:var(--green-dark);font-size:16px}

/* features */
.feature-band{left:0;top:1060px;width:1200px;height:1120px}
.section-title{font-family:"Montserrat",sans-serif;font-size:34px;font-weight:500;text-align:center;width:1200px;left:0}
.features-title{top:1172px;color:var(--white)}
.title-rule{left:570px;width:60px;height:3px;background:var(--white)}
.feature-photo{width:268px;height:268px;border-radius:50%;border:6px solid var(--white)}
.feature-caption{width:340px;text-align:center;color:var(--white);font-size:19px;line-height:1.3}
.btn-white{width:124px;height:42px;background:var(--white);color:var(--green-dark);font-size:14px}
.arrow{width:52px;height:52px;border-radius:50%;display:flex;align-items:center;justify-content:center}

/* testimonials */
.testi-title{top:1748px;color:var(--ink)}
.testi-rule{background:var(--green)}
.testi-card{left:204px;top:1850px;width:1100px;height:240px;background:var(--white);border:2px solid var(--green-light);border-radius:60px}
.quote-mark{left:564px;top:1816px;width:64px;height:64px;border-radius:50%;background:var(--green);color:var(--white);font-family:Georgia,serif;font-size:48px;line-height:72px;text-align:center}
.testi-text{left:252px;top:1904px;width:880px;text-align:center;font-style:italic;font-size:17px;line-height:1.7;color:var(--muted)}
.testi-author{left:252px;top:2030px;width:700px;text-align:center;font-family:"Montserrat",sans-serif;font-size:17px;font-weight:500;color:var(--ink)}

/* contact */
.contact-title{top:2214px;color:var(--ink)}
.toy-photo{left:24px;top:2316px;width:140px;height:260px;border-radius:40px 40px 10px 10px;background:linear-gradient(180deg,#f2c43b 0%,#5aaee0 35%,#e35a4a 65%,#8ac04a 100%);opacity:.85}
.contact-form{left:168px;top:2292px;width:880px;height:330px;border:2px solid var(--green-light);border-radius:40px;background:var(--white)}
.field{height:40px;border:1px solid var(--line);font-size:14px;color:var(--muted);padding:10px 14px}
.submit{left:520px;top:2566px;width:134px;height:44px;background:var(--green);color:var(--white);font-size:17px;border-radius:22px}

/* footer */
.footer{left:0;top:2600px;width:1200px;height:464px}
.foot-col{top:2740px;color:var(--white)}
.foot-col h3{font-family:"Montserrat",sans-serif;font-size:22px;font-weight:500;margin-bottom:14px}
.foot-col li{list-style:none;font-size:14px;line-height:1.85}
.foot-contact li{display:flex;align-items:center;gap:10px}
.foot-contact svg{flex:none}
.copyright{left:0;top:3010px;width:1200px;text-align:center;color:var(--white);font-size:13px}

/* menu overlay */
.menu-veil{left:788px;top:0;width:412px;height:3064px;background:rgba(255,255,255,.86)}
.menu{left:852px;top:60px;list-style:none}
.menu li{font-family:"Montserrat",sans-serif;font-size:17px;font-weight:500;color:var(--ink);line-height:44px}
</style>
</head>
<body>
<div class="canvas">

  <!-- Hero -->
  <div class="abs hero-photo" role="img" aria-label="Photo of a young girl playing with toys in a bright playroom"></div>
  <div class="abs brand"><span>Tumble Nest</span><span style="font-size:13px">Playhouse &amp; Cafe</span></div>
  <div class="abs hero-badge">
    <div class="kicker">Welcome to</div>
    <h1>Tumble Nest<br>Playhouse &amp; Cafe</h1>
    <p>Play, eat and celebrate in a bright and safe space for little ones.</p>
    <div class="dots"><span></span><span></span><span></span><span></span></div>
  </div>

  <!-- About -->
  <div class="abs about-photo" role="img" aria-label="Photo of a baby sitting and stacking colourful building blocks"></div>
  <h2 class="abs about-title">About Tumble Nest<br>Playhouse &amp; Cafe</h2>
  <p class="abs about-text">Tumble Nest is a friendly indoor play centre where children climb, slide and explore while parents relax with fresh coffee. We host birthday parties, holiday programs and vacation care in clean, bright and fully supervised spaces for the whole family.</p>
  <div class="abs btn btn-outline">Read More</div>

  <!-- Features band -->
  <svg class="abs feature-band" viewBox="0 0 1200 1120" preserveAspectRatio="none" aria-hidden="true">
    <defs>
      <linearGradient id="bandGreen" x1="0" y1="0" x2="0" y2="1">
        <stop offset="0" stop-color="#8dcc4e"/>
        <stop offset="0.55" stop-color="#7cc242"/>
        <stop offset="1" stop-color="#a6d86e"/>
      </linearGradient>
    </defs>
    <path d="M0 60 C300 0 600 120 900 60 C1020 36 1120 30 1200 40 L1200 1040 C900 1110 300 1110 0 1040 Z" fill="url(#bandGreen)"/>
    <path d="M0 660 C300 600 900 600 1200 660 L1200 1060 C900 1120 300 1120 0 1060 Z" fill="#ffffff" opacity=".88"/>
  </svg>
  <h2 class="abs section-title features-title">Our Features</h2>
  <div class="abs title-rule" style="top:1226px"></div>

  <div class="abs arrow" style="left:54px;top:1414px;background:rgba(255,255,255,.25);border:2px solid var(--white)">
    <svg width="18" height="18" viewBox="0 0 18 18"><path d="M12 3 L6 9 L12 15" stroke="#fff" stroke-width="2.5" fill="none" stroke-linecap="round"/></svg>
  </div>

  <div class="abs feature-photo" style="left:146px;top:1246px;background:radial-gradient(circle,#f5c9a8 0%,#e48c9c 60%,#c96f8a 100%)" role="img" aria-label="Photo of three smiling girls at a birthday party"></div>
  <div class="abs feature-photo" style="left:466px;top:1246px;background:radial-gradient(circle,#f4d36a 0%,#5ab2e0 45%,#e2514a 75%,#7cc242 100%)" role="img" aria-label="Photo of a child in a ball pit full of coloured balls"></div>
  <div class="abs feature-photo" style="left:786px;top:1246px;background:radial-gradient(circle,#cfe6b6 0%,#9dcf6a 100%)" role="img" aria-label="Photo of children playing on play equipment"></div>

  <div class="abs feature-caption" style="left:110px;top:1540px">Perfect venue for<br>birthdays &amp; private parties</div>
  <div class="abs feature-caption" style="left:430px;top:1540px">4 kids loving<br>party rooms themes</div>
  <div class="abs feature-caption" style="left:750px;top:1540px">Climbing frames<br>and a safe toddler zone</div>
  <div class="abs btn btn-white" style="left:218px;top:1610px">Read More</div>
  <div class="abs btn btn-white" style="left:538px;top:1610px">Read More</div>
  <div class="abs btn btn-white" style="left:858px;top:1610px">Read More</div>

  <!-- Testimonials -->
  <h2 class="abs section-title testi-title">Testimonials</h2>
  <div class="abs title-rule testi-rule" style="top:1800px"></div>
  <div class="abs testi-card"></div>
  <div class="abs quote-mark">&#8220;</div>
  <p class="abs testi-text">Excellent place for kids and parents, amazing party rooms, friendly and helpful staff! I highly recommend for hosting your next party or just to relax while watching your kids have a ball on the play equipment and slides.</p>
  <div class="abs testi-author">By Author Name</div>
  <div class="abs arrow" style="left:134px;top:1944px;background:var(--white);border:2px solid var(--green)">
    <svg width="18" height="18" viewBox="0 0 18 18"><path d="M12 3 L6 9 L12 15" stroke="#5fa52b" stroke-width="2.5" fill="none" stroke-linecap="round"/></svg>
  </div>

  <!-- Contact -->
  <h2 class="abs section-title contact-title">Contact Us</h2>
  <div class="abs title-rule testi-rule" style="top:2266px"></div>
  <div class="abs toy-photo" role="img" aria-label="Photo of a colourful stacking ring toy"></div>
  <div class="abs contact-form"></div>
  <div class="abs field" style="left:200px;top:2328px;width:380px">Name</div>
  <div class="abs field" style="left:600px;top:2328px;width:400px">Email address</div>
  <div class="abs field" style="left:200px;top:2384px;width:380px">Phone</div>
  <div class="abs field" style="left:600px;top:2384px;width:400px">Postcode</div>
  <div class="abs field" style="left:200px;top:2440px;width:800px;height:100px">Message</div>
  <div class="abs btn submit">Submit</div>

  <!-- Footer -->
  <svg class="abs footer" viewBox="0 0 1200 464" preserveAspectRatio="none" aria-hidden="true">
    <defs>
      <linearGradient id="footSun" x1="0" y1="0" x2="0" y2="1">
        <stop offset="0" stop-color="#fcc93a"/>
        <stop offset="1" stop-color="#f7a823"/>
      </linearGradient>
    </defs>
    <path d="M0 60 C300 0 800 90 1200 30 L1200 464 L0 464 Z" fill="url(#footSun)"/>
    <rect x="0" y="390" width="1200" height="74" fill="#e8931a"/>
  </svg>
  <div class="abs foot-col" style="left:128px">
    <h3>Quick Links</h3>
    <ul><li>Home</li><li>Hours &amp; Prices</li><li>Party Packages</li><li>Party Rooms</li></ul>
  </div>
  <div class="abs foot-col" style="left:368px">
    <h3>Resources</h3>
    <ul><li>Vacation Care</li><li>School Holiday Program</li><li>Specials &amp; Promotions</li><li>Gallery</li><li>Contact</li></ul>
  </div>
  <div class="abs foot-col foot-contact" style="left:628px">
    <h3>Contact Us</h3>
    <ul>
      <li><svg width="14" height="14" viewBox="0 0 14 14"><path d="M7 1a4 4 0 0 0-4 4c0 3 4 8 4 8s4-5 4-8a4 4 0 0 0-4-4z" fill="#fff"/><circle cx="7" cy="5" r="1.5" fill="#f7a823"/></svg>12 Wattle Street, Brookvale NSW 2100</li>
      <li><svg width="14" height="14" viewBox="0 0 14 14"><path d="M3 1l2 3-1.5 1.5a8 8 0 0 0 5 5L10 9l3 2-1 2c-6 0-11-5-11-11z" fill="#fff"/></svg>02 9000 1234</li>
      <li><svg width="14" height="14" viewBox="0 0 14 14"><rect x="1" y="4" width="12" height="8" rx="1" fill="#fff"/><rect x="3" y="1" width="8" height="4" fill="#fff"/></svg>02 9000 1235</li>
      <li><svg width="14" height="14" viewBox="0 0 14 14"><rect x="1" y="3" width="12" height="8" rx="1" fill="#fff"/><path d="M1 3l6 5 6-5" stroke="#f7a823" fill="none"/></svg>hello@tumblenest.com.au</li>
    </ul>
  </div>
  <div class="abs copyright">&copy; 2016 Tumble Nest. All rights reserved.</div>

  <!-- Menu overlay -->
  <div class="abs menu-veil"></div>
  <svg class="abs" style="left:1010px;top:46px" width="50" height="30" viewBox="0 0 50 30" aria-hidden="true">
    <rect x="0" y="2" width="50" height="4" fill="#999"/><rect x="0" y="13" width="50" height="4" fill="#999"/><rect x="0" y="24" width="50" height="4" fill="#999"/>
  </svg>
  <svg class="abs" style="left:1140px;top:28px" width="36" height="36" viewBox="0 0 36 36" aria-label="Close menu">
    <path d="M4 4 L32 32 M32 4 L4 32" stroke="#555" stroke-width="4" stroke-linecap="round"/>
  </svg>
  <ul class="abs menu">
    <li>Home</li><li>Hours &amp; Prices</li><li>Party Packages</li><li>Party Rooms</li><li>Vacation Care</li><li>School Holiday Program</li><li>Specials &amp; Promotions</li><li>Gallery</li><li>Contact</li>
  </ul>

</div>
</body>
</html>
```